Wellness Coach/Personal trainer needs wordpress site/blog with ecommerce capable membership area

We need a WordPress design for FitPennyCoach.com. This is a blog about wellness, weight loss, and health related topics. Design logo will be provided to the winner.

A great site with a design that we would like to emulate are http://qv4.example. The design should be simple, clean, unique, fun, and distinctive. Above all, it should be highly readable and easy to navigate.

These are the specific sections/categories of the blog that should be included and incorporated into the design SEE BELOW.

Thanks in advance for your consideration
Updates

Project Deadline Extended
Reason: I have extended the deadline to evaluate more designs from other pros

Hello all, Please take a minute to review the requirements for this project and please make sure you are capable of meeting ALL the requirements. As you already know I will be making a decision very shortly on whose design I will be moving forward with, if there are any last minute submissions now is the time. Thank you for your time.

Target Market(s)

90 % women 10 % men my clients are usually professionals who value their appearance, health, longevity and time.

Industry/Entity Type

Personal Trainer

Font styles to use
Serif

Colors
886aae
ffcf3e

Requirements
Must have
• Requirements

- start losing weight today.... 555 207 9184 (first line)
- visuals/images and backgrounds to give the idea of wellness, weight loss, healthy living, etc
- navigation menu - home, who we are, what we do, who we serve, blog, contact, members area

1) slider element at top below navigation menu
2) slider element near bottom of page will have testimonials
3) contact form/inquiry form (one page)
4) will provide wellness logo (to give credibility)
5) color scheme purple, gold and white
6) membership area
7) fb, tw, youtube icons
8) footer area - In the footer, there will be smaller company logo, copyright,
disclaimer, privacy policy, terms n conditions, verse of day, and contact info, Phone: (555) 207-9184
Email: support@...
Address:
9) use dummy content/graphic as they will be replaced by real content (the winner will provide instruction on how to make changes to all text and changing graphics)
9) ecommerce enabled / newsletter signup area

```html
<!DOCTYPE html>
<html lang="en">
<head>
<meta charset="utf-8">
<title>Fit Penny Coach</title>
<link rel="stylesheet" href="https://fonts.googleapis.com/css2?family=Open+Sans:ital,wght@0,400;0,600;0,700;1,400&display=swap">
<style>
:root{
  --purple:#7b5f8d;
  --purple-dark:#6a4f7c;
  --purple-text:#6b5478;
  --purple-band:#7a5e86;
  --btn:#7b6386;
  --ink:#3c3c3c;
  --muted:#a8a8a8;
  --light:#f2f2f2;
  --footer:#2f2f2f;
  --footer-bar:#242424;
  --white:#ffffff;
}
*{box-sizing:border-box;margin:0;padding:0}
html,body{width:1200px;height:3093px;overflow:hidden}
body{font-family:"Open Sans",Arial,sans-serif;color:var(--ink);background:var(--white);position:relative}
.abs{position:absolute}
/* header */
.site-header{position:absolute;left:0;top:0;width:1200px;height:107px;border-top:4px solid var(--purple)}
.brand{position:absolute;left:93px;top:34px;display:flex;align-items:center;gap:12px;font-size:29px;font-weight:600;color:var(--purple-text)}
.brand-dot{width:24px;height:24px;border-radius:50%;background:var(--purple)}
.tagline{position:absolute;right:93px;top:36px;font-size:21px;color:#555}
.tagline b{font-weight:700;color:#444}
/* nav */
.main-nav{position:absolute;left:0;top:107px;width:1200px;height:68px;background:linear-gradient(#8a6d9c,var(--purple))}
.main-nav ul{list-style:none;position:absolute;left:93px;top:0;width:1014px;height:68px;display:flex}
.main-nav li{flex:1;display:flex;align-items:center;justify-content:center;font-size:13px;color:var(--white);border-right:1px solid rgba(255,255,255,.12);letter-spacing:.3px}
.main-nav li.active{background:var(--purple-dark)}
/* hero */
.hero{position:absolute;left:0;top:175px;width:1200px;height:621px;background:linear-gradient(180deg,#c9ccd0 0%,#eee6c8 35%,#c9b567 70%,#7e8a3c 100%)}
.hero-arrow{position:absolute;top:272px;width:64px;height:64px}
/* section headings */
.section-title{position:absolute;left:0;width:1200px;text-align:center;font-size:19px;font-weight:700;color:var(--purple-text);letter-spacing:.3px}
.divider{position:absolute;left:450px;width:300px;height:20px}
/* blog */
.post{position:absolute;top:924px;width:315px}
.post-image{width:315px;height:235px}
.post-title{margin-top:37px;font-size:15px;font-weight:600;color:var(--purple-text)}
.share{margin-top:13px;display:flex;gap:4px}
.share span{width:22px;height:22px;background:#6d7fa8;border-radius:2px}
.share span.wide{width:48px;background:#5b7cb8}
.post-excerpt{margin-top:13px;font-size:12.5px;line-height:21px;color:var(--muted)}
.read-more{margin-top:25px;width:113px;height:45px;background:var(--btn);color:var(--white);font-size:11.5px;display:flex;align-items:center;justify-content:center;border-radius:2px}
/* membership */
.membership{position:absolute;left:0;top:1485px;width:1200px;height:488px;background:var(--light)}
.member{position:absolute;top:146px;width:237px;text-align:center}
.member-image{width:237px;height:192px}
.member-name{margin-top:29px;font-size:14.5px;font-weight:700;color:var(--purple-text)}
.member-text{margin-top:6px;font-size:12.5px;line-height:20px;color:var(--muted)}
/* contact */
.contact{position:absolute;left:0;top:1973px;width:1200px;height:448px;background:var(--purple-band)}
.field{position:absolute;background:var(--white);border-radius:2px;font-size:12px;color:#777;padding:0 14px;display:flex;align-items:center}
.field.area{align-items:flex-start;padding-top:12px}
.submit{position:absolute;left:95px;top:336px;width:154px;height:58px;background:#3a3a3a;color:var(--white);font-size:14px;font-weight:600;display:flex;align-items:center;justify-content:center}
/* testimonials */
.quote{position:absolute;top:2569px;width:484px;font-size:12.5px;line-height:21px;font-style:italic;color:#888}
.quote-name{margin-top:16px;font-size:17px;color:var(--ink)}
.dots{position:absolute;top:2742px;left:571px;display:flex;gap:4px}
.dots span{width:13px;height:13px;border-radius:50%;background:#ccc}
.dots span.on{background:#9a88a6}
/* footer */
.site-footer{position:absolute;left:0;top:2784px;width:1200px;height:237px;background:var(--footer);color:#ddd}
.footer-brand{position:absolute;left:99px;top:60px;display:flex;align-items:center;gap:10px;font-size:19px;font-weight:700;color:var(--white)}
.footer-brand .brand-dot{width:20px;height:20px}
.socials{position:absolute;left:91px;top:158px;display:flex;gap:8px}
.socials span{width:34px;height:34px;border-radius:50%}
.footer-title{position:absolute;top:54px;font-size:15px;font-weight:600;color:var(--white)}
.footer-line{position:absolute;display:flex;align-items:center;gap:16px;font-size:12.5px;color:#ddd}
.icon-chip{width:34px;height:34px;border-radius:50%;background:#3c3c3c;display:flex;align-items:center;justify-content:center}
.news-input{position:absolute;left:913px;top:136px;width:194px;height:33px;background:#3a3a3a;font-size:11px;color:#999;display:flex;align-items:center;padding:0 10px;justify-content:space-between}
.footer-bar{position:absolute;left:0;top:3021px;width:1200px;height:72px;background:var(--footer-bar);color:#aaa;font-size:11.5px;display:flex;align-items:center;justify-content:center}
</style>
</head>
<body>

<header class="site-header">
  <div class="brand"><span class="brand-dot"></span>Fit Penny Coach</div>
  <div class="tagline">Start losing weight <b>TODAY.... 555 207 9184</b></div>
</header>

<nav class="main-nav">
  <ul>
    <li class="active">HOME</li><li>WHO WE ARE</li><li>WHAT WE DO</li><li>WHO WE SERVE</li><li>CONTACT</li><li>BLOG</li><li>MEMBERS</li>
  </ul>
</nav>

<section class="hero" role="img" aria-label="Slider photo: four women with arms raised in a sunny grass field">
  <svg class="hero-arrow" style="left:22px" viewBox="0 0 64 64"><circle cx="32" cy="32" r="29" fill="rgba(255,255,255,.25)" stroke="#fff" stroke-width="3"/><path d="M37 20 L24 32 L37 44" fill="none" stroke="#fff" stroke-width="4"/></svg>
  <svg class="hero-arrow" style="left:1112px" viewBox="0 0 64 64"><circle cx="32" cy="32" r="29" fill="rgba(255,255,255,.25)" stroke="#fff" stroke-width="3"/><path d="M27 20 L40 32 L27 44" fill="none" stroke="#fff" stroke-width="4"/></svg>
</section>

<h2 class="section-title" style="top:832px">RECENT BLOG ARTICLES</h2>
<svg class="divider" style="top:875px" viewBox="0 0 300 20"><line x1="0" y1="10" x2="300" y2="10" stroke="#ddd"/><rect x="143" y="3" width="14" height="14" transform="rotate(45 150 10)" fill="var(--purple-text)"/></svg>

<article class="post" style="left:93px">
  <div class="post-image" role="img" aria-label="Woman meditating on green grass" style="background:linear-gradient(135deg,#3f7d1e,#9ccc4a 60%,#e9e9e4)"></div>
  <h3 class="post-title">ABOUT WELLNESS</h3>
  <div class="share"><span></span><span style="background:#b85a4e"></span><span style="background:#5fa9d8"></span><span class="wide"></span></div>
  <p class="post-excerpt">Sed ut perspiciatis unde omnis iste natus error sit voluptatem accusantium doloremque laudantium, totam rem aperiam, eaque ipsa quae ab illo inventore veritatis et quasi architecto beatae.</p>
  <div class="read-more">READ MORE</div>
</article>
<article class="post" style="left:441px">
  <div class="post-image" role="img" aria-label="Women celebrating weight loss with a trainer" style="background:linear-gradient(135deg,#d9e2ea,#c9a79a 50%,#e04a6a 70%,#7fb6d6)"></div>
  <h3 class="post-title">WEIGHT LOSS</h3>
  <div class="share"><span></span><span style="background:#b85a4e"></span><span style="background:#5fa9d8"></span><span class="wide"></span></div>
  <p class="post-excerpt">Sed ut perspiciatis unde omnis iste natus error sit voluptatem accusantium doloremque laudantium, totam rem aperiam, eaque ipsa quae ab illo inventore veritatis et quasi architecto beatae.</p>
  <div class="read-more">READ MORE</div>
</article>
<article class="post" style="left:792px">
  <div class="post-image" role="img" aria-label="Family talking with a health advisor" style="background:linear-gradient(135deg,#8a7f78,#e6d6c6 50%,#4d6e93)"></div>
  <h3 class="post-title">HEALTH</h3>
  <div class="share"><span></span><span style="background:#b85a4e"></span><span style="background:#5fa9d8"></span><span class="wide"></span></div>
  <p class="post-excerpt">Sed ut perspiciatis unde omnis iste natus error sit voluptatem accusantium doloremque laudantium, totam rem aperiam, eaque ipsa quae ab illo inventore veritatis et quasi architecto beatae.</p>
  <div class="read-more">READ MORE</div>
</article>

<section class="membership">
  <h2 class="section-title" style="top:57px">OUR MEMBERSHIP</h2>
  <svg class="divider" style="top:87px" viewBox="0 0 300 20"><line x1="0" y1="10" x2="300" y2="10" stroke="#ddd"/><rect x="143" y="3" width="14" height="14" transform="rotate(45 150 10)" fill="var(--purple-text)"/></svg>
  <div class="member" style="left:93px"><div class="member-image" role="img" aria-label="Portrait of a smiling member" style="background:linear-gradient(135deg,#c97a4a,#f1c9a0 60%,#e8e0d0)"></div><h3 class="member-name">SED UT PERSPICIAT</h3><p class="member-text">Sed ut perspiciatis unde omnis iste natus error sit voluptatem</p></div>
  <div class="member" style="left:355px"><div class="member-image" role="img" aria-label="Portrait of a member" style="background:linear-gradient(135deg,#f4f4f4,#d9b9a4 50%,#5a3a2a)"></div><h3 class="member-name">SED UT PERSPICIAT</h3><p class="member-text">Sed ut perspiciatis unde omnis iste natus error sit voluptatem</p></div>
  <div class="member" style="left:613px"><div class="member-image" role="img" aria-label="Portrait of a laughing member in a sun hat" style="background:linear-gradient(135deg,#8fb4d8,#c9a57a 55%,#f1d27a)"></div><h3 class="member-name">SED UT PERSPICIAT</h3><p class="member-text">Sed ut perspiciatis unde omnis iste natus error sit voluptatem</p></div>
  <div class="member" style="left:870px"><div class="member-image" role="img" aria-label="Portrait of a member with a flower in her hair" style="background:linear-gradient(135deg,#2a2020,#e6c4b0 55%,#fafafa)"></div><h3 class="member-name">SED UT PERSPICIAT</h3><p class="member-text">Sed ut perspiciatis unde omnis iste natus error sit voluptatem</p></div>
</section>

<section class="contact">
  <h2 class="section-title" style="top:54px;color:var(--white)">CONTACT FORM</h2>
  <svg class="divider" style="top:84px" viewBox="0 0 300 20"><line x1="0" y1="10" x2="300" y2="10" stroke="rgba(255,255,255,.35)"/><rect x="143" y="3" width="14" height="14" transform="rotate(45 150 10)" fill="#fff"/></svg>
  <div class="field" style="left:93px;top:138px;width:266px;height:52px">Name:</div>
  <div class="field" style="left:373px;top:138px;width:264px;height:52px">Last Name:</div>
  <div class="field area" style="left:647px;top:138px;width:460px;height:180px">Message:</div>
  <div class="field" style="left:93px;top:204px;width:266px;height:50px">Email:</div>
  <div class="field" style="left:373px;top:204px;width:264px;height:50px">Phone:</div>
  <div class="field" style="left:93px;top:268px;width:544px;height:52px;justify-content:space-between">Fit Penny Coach Topic<svg width="12" height="8" viewBox="0 0 12 8"><path d="M0 0H12L6 8Z" fill="#333"/></svg></div>
  <div class="submit">SUBMIT</div>
</section>

<h2 class="section-title" style="top:2463px">TESTIMONIALS</h2>
<svg class="divider" style="top:2506px" viewBox="0 0 300 20"><line x1="0" y1="10" x2="300" y2="10" stroke="#ddd"/><rect x="143" y="3" width="14" height="14" transform="rotate(45 150 10)" fill="var(--purple-text)"/></svg>
<blockquote class="quote" style="left:93px">“ Sed ut perspiciatis unde omnis iste natus error sit voluptatem accusantium doloremque laudantium, totam rem aperiam, eaque ipsa quae ab illo inventore veritatis et quasi architecto beatae vitae dicta sunt explicabo. Nemo enim ipsam voluptatem quia voluptas sit aspernatur aut odit aut fugit, sed”<p class="quote-name">Dana Whitfield, 13-11-2014</p></blockquote>
<blockquote class="quote" style="left:629px">“ Sed ut perspiciatis unde omnis iste natus error sit voluptatem accusantium doloremque laudantium, totam rem aperiam, eaque ipsa quae ab illo inventore veritatis et quasi architecto beatae vitae dicta sunt explicabo. Nemo enim ipsam voluptatem quia voluptas sit aspernatur aut odit aut fugit, sed”<p class="quote-name">Dana Whitfield, 13-11-2014</p></blockquote>
<div class="dots"><span></span><span></span><span class="on"></span><span></span></div>

<footer class="site-footer">
  <div class="footer-brand"><span class="brand-dot" style="background:#8a6d9c"></span>Fit Penny Coach</div>
  <div class="socials"><span style="background:#3b5c9e"></span><span style="background:#3fa3dc"></span><span style="background:#555"></span><span style="background:#d9302a"></span></div>

  <h4 class="footer-title" style="left:342px">CONTACT INFO</h4>
  <div class="footer-line" style="left:342px;top:100px"><span class="icon-chip"><svg width="14" height="14" viewBox="0 0 24 24"><path d="M6.6 10.8a15 15 0 006.6 6.6l2.2-2.2c.3-.3.7-.4 1-.2 1.1.4 2.3.6 3.6.6.6 0 1 .4 1 1V20c0 .6-.4 1-1 1A17 17 0 013 4c0-.6.4-1 1-1h3.5c.6 0 1 .4 1 1 0 1.3.2 2.5.6 3.6.1.3 0 .7-.2 1z" fill="#ccc"/></svg></span>Phone: (555) 207-9184</div>
  <div class="footer-line" style="left:342px;top:158px"><span class="icon-chip"><svg width="14" height="11" viewBox="0 0 14 11"><rect width="14" height="11" rx="1" fill="#ccc"/><path d="M0 1L7 6L14 1" fill="none" stroke="#3c3c3c" stroke-width="1.4"/></svg></span>Email: support@...</div>

  <h4 class="footer-title" style="left:631px">ADDRESS:</h4>
  <div class="footer-line" style="left:631px;top:96px;align-items:flex-start"><span class="icon-chip"><svg width="12" height="16" viewBox="0 0 12 16"><path d="M6 0a6 6 0 00-6 6c0 4.5 6 10 6 10s6-5.5 6-10a6 6 0 00-6-6z" fill="#ccc"/><circle cx="6" cy="6" r="2.2" fill="#3c3c3c"/></svg></span><span style="line-height:23px">4810 Maple Grove Lane,<br>Cedar Falls, Lorem Street,<br>Oregon 97005</span></div>

  <h4 class="footer-title" style="left:913px">NEWSLETTER</h4>
  <p class="abs" style="left:913px;top:104px;font-size:12.5px;color:#ddd">Sed ut perspiciatis ulob nSed</p>
  <div class="news-input">email<svg width="7" height="9" viewBox="0 0 7 9"><path d="M0 0L7 4.5L0 9Z" fill="#bbb"/></svg></div>
</footer>
<div class="footer-bar">©2014 copyright, disclaimer, privacy policy, terms n conditions, verse of day.</div>

</body>
</html>
```